Elegant, High End Integrated Wellness Healthcare Practice

We need a brochure designed for an integrated mind-body wellness healthcare practice (www.quellarivecare.com) . This brochure will be used when we cold call prospects (physicians to refer to our office, and potential consumers to utilize our services). Our practice is geographically located in the middle Tennessee USA region, although we have plans to become an international company as many of our offerings can be accessed anywhere in the world. Ultimately our goal is to have this brochure used as a leave-behind in an effort to introduce our integrated offerings to increase market share. The final product brochure should be both elegant and serious, with clean lines but also convey warmth and trust, as individuals who are coming for our services have usually struggled with their health for a significant amount of time before finding our practice.
Updates

The design brief was very specific about providing a high-end science-based 2-page brochure (not flier). Several designs submitted were fliers. The other designs were heavy on yoga or "woo woo" non-science-based looking pictures. This is a flier to appeal to physicians and other healthcare providers. Therefore the design must speak science and evidence-based methods of mind and body wellness care. I would also like to appeal to the other designers I paid extra for their submissions and who have indicated they will "respond in the coming days."

```html
<!DOCTYPE html>
<html lang="en">
<head>
<meta charset="utf-8">
<title>Quellarive Wellness – Brochure</title>
<link rel="stylesheet" href="https://fonts.googleapis.com/css2?family=Noto+Serif:wght@400;700&family=Source+Serif+4:opsz,wght@8..60,400&family=Cinzel:wght@400&family=Poppins:wght@400&display=swap">
<style>
:root{
  --backdrop:#808080;
  --paper:#ffffff;
  --green-dark:#213a0c;
  --green-mid:#7ba556;
  --green-pale:#e7efdf;
  --ink:#3b3b3b;
  --link:#2a3fb8;
  --photo-a:#e9c9a0;
  --photo-b:#8f7763;
}
*{margin:0;padding:0;box-sizing:border-box}
html,body{width:1200px;height:863px;overflow:hidden;background:var(--backdrop)}
.spread{position:absolute;left:21px;top:23px;width:1158px;height:816px;display:flex}
.page{position:relative;width:579px;height:816px;background:var(--paper);overflow:hidden}

.brand{position:absolute;display:flex;align-items:center;gap:7px}
.brand-dot{width:38px;height:38px;border-radius:50%;border:3px solid var(--green-mid);background:var(--green-dark)}
.brand-name{font-family:"Noto Serif",serif;font-weight:400;color:var(--green-dark);font-size:15px;line-height:19px;font-variant:small-caps;letter-spacing:.3px}

/* cover */
.cover .brand{left:21px;top:27px}
.hero{position:absolute;left:0;top:0}
.cover-title{position:absolute;left:18px;top:262px;font-family:"Noto Serif",serif;font-weight:700;color:var(--green-dark);font-size:38px;line-height:49px}
.toc-title{position:absolute;left:19px;top:490px;font-family:"Noto Serif",serif;font-weight:700;color:var(--green-mid);font-size:29px}
.toc{position:absolute;left:0;top:546px;width:579px;height:150px}
.toc-item{position:absolute;top:0;width:88px}
.toc-photo{width:79px;height:79px;border-radius:50%}
.toc-label{margin-top:9px;padding-left:2px;font-family:"Noto Serif",serif;font-weight:700;color:var(--green-dark);font-size:11.6px;line-height:15.5px}
.wave{position:absolute;left:0;bottom:0}
.cover-contact{position:absolute;left:0;width:579px;top:760px;text-align:center;font-family:"Noto Serif",serif;font-weight:700;color:#fff;font-size:11.8px;line-height:19px}

/* inside */
.inside .brand{left:21px;top:15px}
.values-title{position:absolute;left:28px;top:70px;font-family:"Noto Serif",serif;font-weight:400;color:var(--green-dark);font-size:29px}
.col{position:absolute;top:126px;width:248px;font-family:"Source Serif 4",serif;color:var(--ink);font-size:8.6px;line-height:12.6px}
.col-a{left:28px}
.col-b{left:299px}
.col h2{font-family:"Noto Serif",serif;font-weight:700;color:var(--green-dark);font-size:11.8px;margin:0 0 9px}
.col p{margin:0 0 4.5px;text-align:justify;hyphens:auto}
.col p+h2{margin-top:9px}
.col-a h2.spaced{margin-top:16px}
.contact{position:absolute;left:299px;top:563px;width:248px;text-align:center;border-top:1px solid #f1f1f1;padding-top:8px}
.contact-head{font-family:"Cinzel",serif;color:var(--green-mid);font-size:12px;margin:4px 0 6px}
.contact a{display:block;font-family:"Poppins",sans-serif;font-size:9.4px;color:var(--link);margin-bottom:5px}
.social{position:absolute;left:189px;top:758px;display:flex;gap:4px}
.social span{width:25px;height:25px;border-radius:50%;border:2px solid var(--green-dark);box-shadow:inset 0 0 0 2px var(--green-mid)}
</style>
</head>
<body>
<div class="spread">

  <section class="page cover">
    <svg class="hero" width="579" height="816" viewBox="0 0 579 816">
      <defs>
        <radialGradient id="glow" cx="0.55" cy="0.6" r="0.6">
          <stop offset="0" stop-color="#fff3d6"/>
          <stop offset="0.35" stop-color="var(--photo-a)"/>
          <stop offset="1" stop-color="var(--photo-b)"/>
        </radialGradient>
      </defs>
      <path d="M222 -2 A 240 240 0 0 0 226 336" fill="none" stroke="var(--green-mid)" stroke-width="4"/>
      <circle cx="515" cy="140" r="336" fill="var(--green-dark)"/>
      <circle cx="502" cy="141" r="311" fill="url(#glow)" role="img" aria-label="Photo of cupped hands holding a glowing brain network against a warm sunset field"/>
    </svg>
    <div class="brand"><span class="brand-dot"></span><span class="brand-name">Quellarive<br>Wellness</span></div>

    <h1 class="cover-title">Methods<br>Of Mind<br>And Body<br>Wellness Care</h1>
    <h2 class="toc-title">Table of Contents:</h2>

    <div class="toc">
      <div class="toc-item" style="left:18px"><div class="toc-photo" role="img" aria-label="Photo of a woman relaxing outdoors" style="background:radial-gradient(circle,#c9a27f,#6f6a52)"></div><div class="toc-label" style="margin-top:4px">An Integrative Approach</div></div>
      <div class="toc-item" style="left:136px"><div class="toc-photo" role="img" aria-label="Photo of a woman eating a healthy meal" style="background:radial-gradient(circle,#b8b2a6,#5f6a6a)"></div><div class="toc-label">Personalized Care</div></div>
      <div class="toc-item" style="left:247px"><div class="toc-photo" role="img" aria-label="Photo of people exercising together outdoors" style="background:radial-gradient(circle,#d9d8d0,#7c8c7a)"></div><div class="toc-label">Innovative Treatments</div></div>
      <div class="toc-item" style="left:358px"><div class="toc-photo" role="img" aria-label="Photo of a hand holding a glowing brain at sunset" style="background:radial-gradient(circle,#f4b864,#4f3f36)"></div><div class="toc-label">Root Cause Resolution</div></div>
      <div class="toc-item" style="left:469px"><div class="toc-photo" role="img" aria-label="Photo of a person raising arms at sunrise" style="background:radial-gradient(circle,#f2c35c,#6b5a3a)"></div><div class="toc-label">Co-Creating Health</div></div>
    </div>

    <svg class="wave" width="579" height="120" viewBox="0 0 579 120">
      <path d="M0 7 C60 30 120 50 170 40 C250 22 300 -5 380 5 C460 15 520 30 579 0 L579 120 L0 120 Z" fill="var(--green-mid)"/>
    </svg>
    <p class="cover-contact">480 Linden Hollow Rd. Ashford Mills, TN 37190.<br>Quellarive Wellness - Call (555) 014-2290</p>
  </section>

  <section class="page inside">
    <div class="brand"><span class="brand-dot"></span><span class="brand-name">Quellarive<br>Wellness</span></div>
    <h1 class="values-title">Core Values of Care</h1>

    <div class="col col-a">
      <h2>1. An Integrative Approach</h2>
      <p style="text-align:left">Join us in our mission to change healthcare as we know it. Guided step-by-step by our care team, well embark on an integrative approach to cover more of the issues we face across the lifespan. Dedicated Attention</p>
      <p>People are more confused than ever when it comes to their health and they don’t know WHO or WHAT to believe. Taking charge of your health requires much more than just your typical 7-minute doctor’s visit, which can’t even cover the basics of what you need to know to heal.</p>
      <p>During your in-depth intake consultation, we take the time needed, one-on-one, to thoroughly explore the unique health concerns that keep you from living your best life.</p>
      <h2>2. Personalized Care</h2>
      <p>This is no “one-size-fits-all” when it comes to giving yourself the best care. Everyone is biologically unique, and as we age, we have different needs and requirements.</p>
      <p>First we get to the bottom of your worst symptoms with advanced lab evaluation. After we craft your personalized and targeted healing plan, we also empower you with the knowledge and tools to choose a smarter lifestyle that supports your healing so you don’t find yourself right back where you started a year later.</p>
      <h2 class="spaced">3. Innovative Treatments</h2>
      <p>Did you know that it takes on average 17 years for clinical breakthroughs to make their way into your conventional doctor’s office? That means many health care practitioners are dispensing outdated advice and not using the best evaluation techniques for your particular symptoms and circumstances. Chances are they are not even aware of the proper evaluation that could make all the difference in your healing plan.</p>
      <p>At Quellarive Wellness we provide the best of both worlds...traditional approaches in body &amp; mind health with clinicians who also have advanced training in functional medicine – to deliver the best, most advanced evaluation paired with current treatments and nutritional science so that we can look beyond symptoms to provide solutions to your mind and body health concerns.</p>
    </div>

    <div class="col col-b">
      <h2>4. Root Cause Resolution</h2>
      <p style="text-align:left">We get to the bottom of WHY you feel sluggish, depressed, anxious, distracted, can’t release stubborn weight, or struggle with brain fog.</p>
      <p style="text-align:left">Traditional outdated healthcare models focus on treating symptoms and ignore the core reason(s) behind why things you have tried aren’t working. Our practice uses the tools often found in functional medicine, including a more complete evaluation to see the factors and reasons behind why you are stuck. Many people are struggling with neurotransmitter deficiencies, nutritional deficits, stealth infections, toxicity, potential food intolerances and allergies, and gut &amp; hormonal imbalances that are not traditionally detected by conventional medical evaluation.</p>
      <h2>4. Co-Creating Health</h2>
      <p style="text-align:left">Changing your lifestyle may seem daunting, but we also equip you with mindset tools &amp; mentorship to overcome life habits that are an impediment to optimal wellness.</p>
      <p style="text-align:left">We make the prospect of getting healthy “enjoyable.” We have a wide range of tools to support you during your body &amp; mind health transformation and help build resilience and regain energy. We do this through the Quellarive Balance (QB) Method.</p>
      <p style="text-align:left">We also leverage health coaching and other forms of support &amp; accountability so your new healing lifestyle will become an integral part of your everyday life. We also harness the support of online communities to give you support remotely, as you make important health changes. We serve clients in Ashford Mills, Brenwick, Dalton Ridge, Fairmere, Corby Falls, Lindale Grove TN, and surrounding areas.</p>
    </div>

    <div class="contact">
      <p class="contact-head">Quellarive Wellness</p>
      <a href="#">480 Linden Hollow Rd. Ashford Mills, TN 37190</a>
      <a href="#">Call Now</a>
      <p class="contact-head">Operating Hours</p>
      <a href="#">Monday - Friday: 8am - 7pm</a>
    </div>

    <svg class="wave" width="579" height="120" viewBox="0 0 579 120">
      <path d="M0 0 C60 30 120 50 200 40 C280 30 320 -5 400 3 C470 10 530 30 579 5 L579 120 L0 120 Z" fill="var(--green-pale)"/>
    </svg>
    <div class="social" aria-label="Social media links">
      <span></span><span></span><span></span><span></span><span></span><span></span><span></span>
    </div>
  </section>

</div>
</body>
</html>
```